Lumbrix Design

Looking for Lumbrix banner and square design:
Lumbrix Banner
W:1600 px H:400 px
Square
120x120

Logo attached.

Description: Data-Driven stock market portfolio management using quantitative analysis.

```html
<!DOCTYPE html>
<html lang="en">
<head>
<meta charset="utf-8">
<title>Lumbrix – Banner and Square</title>
<link rel="stylesheet" href="https://fonts.googleapis.com/css2?family=Montserrat:wght@400;600;700&display=swap">
<style>
  :root {
    --sheet-bg: #ffffff;
    --label-grey: #cccccc;
    --panel-navy: #155a82;
    --brand-blue: #0a78bf;
    --brand-navy: #145a84;
    --text-light: #ffffff;
    --shadow: rgba(0, 0, 0, 0.55);
  }
  * { box-sizing: border-box; margin: 0; padding: 0; }
  html, body {
    width: 1200px;
    height: 1007px;
    overflow: hidden;
    background: var(--sheet-bg);
    font-family: "Montserrat", Arial, sans-serif;
  }
  .sheet {
    position: relative;
    width: 1200px;
    height: 1007px;
  }
  .size-label {
    position: absolute;
    left: 0;
    width: 1200px;
    text-align: center;
    color: var(--label-grey);
    font-weight: 700;
    font-size: 40px;
    line-height: 1;
    letter-spacing: 0.5px;
  }
  .size-label--banner { top: 150px; left: 36px; }
  .size-label--square { top: 872px; left: 40px; }

  /* Banner 1600 x 400 */
  .banner {
    position: absolute;
    left: 109px;
    top: 235px;
    width: 1024px;
    height: 253px;
    background: var(--sheet-bg);
    box-shadow: 2px 2px 2px var(--shadow);
    overflow: hidden;
  }
  .banner__panel {
    position: absolute;
    left: 449px;
    top: 0;
    width: 575px;
    height: 253px;
    background: var(--panel-navy);
  }
  .banner__brand {
    position: absolute;
    left: 45px;
    top: 96px;
    display: flex;
    align-items: center;
    gap: 14px;
  }
  .brand-dot {
    width: 66px;
    height: 66px;
    border-radius: 50%;
    background: var(--brand-blue);
    flex: none;
  }
  .brand-name {
    color: var(--brand-navy);
    font-weight: 600;
    font-size: 40px;
    line-height: 1;
    letter-spacing: 1px;
  }
  .banner__tagline {
    position: absolute;
    left: 637px;
    top: 60px;
    color: var(--text-light);
    font-weight: 700;
    font-size: 30px;
    line-height: 37px;
    letter-spacing: 0.5px;
  }
  .banner__tagline span { display: block; white-space: nowrap; }
  .banner__tagline .indent { padding-left: 9px; }

  /* Square 120 x 120 */
  .square {
    position: absolute;
    left: 522px;
    top: 601px;
    width: 228px;
    height: 228px;
    background: var(--sheet-bg);
    box-shadow: 2px 2px 2px var(--shadow);
    display: flex;
    flex-direction: column;
    align-items: center;
  }
  .square .brand-dot {
    width: 104px;
    height: 104px;
    margin-top: 29px;
  }
  .square .brand-name {
    margin-top: 30px;
    font-size: 34px;
  }
</style>
</head>
<body>
<main class="sheet">
  <p class="size-label size-label--banner">W:1600 px H:400 px</p>

  <section class="banner" aria-label="Lumbrix banner">
    <div class="banner__panel"></div>
    <div class="banner__brand">
      <span class="brand-dot"></span>
      <span class="brand-name">Lumbrix</span>
    </div>
    <h1 class="banner__tagline">
      <span>Data-Driven stock</span>
      <span class="indent">market portfolio</span>
      <span>management using</span>
      <span>quantitative analysis</span>
    </h1>
  </section>

  <section class="square" aria-label="Lumbrix square">
    <span class="brand-dot"></span>
    <span class="brand-name">Lumbrix</span>
  </section>

  <p class="size-label size-label--square">W:120px H:120 px</p>
</main>
</body>
</html>
```